Web Design Project

Desisgn a new style for the proposed website as per the attached link. The logo will remain as is, and it is likely that the colours will be as per the attached style guide.

Otherwise look and feel, icons, layout, images are within scope.

Current prosposed home page:
http://vantrelux-newsite.pagemorrowhost.com/index

Target Market(s)

Typically, large organisations from any industry such as Airlines, banks, Govt agencies.

Could be operational executives, business improvement specialists, bsuienss analysts.

```html
<!DOCTYPE html>
<html lang="en">
<head>
<meta charset="utf-8">
<title>Vantrelux — Home</title>
<link href="https://fonts.googleapis.com/css2?family=Arimo:ital,wght@0,400;0,700;1,700&family=Roboto+Condensed:wght@700&display=swap" rel="stylesheet">
<style>
:root{
  --brand:#1a8bbf;
  --text:#555;
  --muted:#8a8a8a;
  --rule:#d9d9d9;
  --frame:#3a3a3a;
  --tab:#2f2f2f;
  --tab-active:#b4b4b4;
  --panel:rgba(110,110,110,.92);
  --footer-bg:#dcdcdc;
  --white:#fff;
}
*{box-sizing:border-box;margin:0;padding:0}
html,body{width:825px;height:1200px;overflow:hidden;background:var(--white)}
body{position:relative;font-family:"Arimo",Arial,sans-serif;color:var(--text);font-size:9px}
a{color:inherit;text-decoration:none}
h2,h3,h5{font-weight:400}
.abs{position:absolute}

.top-strip{left:0;top:0;width:825px;height:9px;background:linear-gradient(#4d9dc6,#8cc4e0);border-bottom:2px solid #cfe6f2}

.brand{left:48px;top:38px;display:flex;align-items:center;gap:10px}
.brand-dot{width:30px;height:30px;border-radius:50%;background:var(--brand)}
.brand-name{font-size:27px;color:var(--brand);font-weight:400;letter-spacing:.5px}

.search{left:593px;top:27px;width:183px;height:26px;background:linear-gradient(#f4f4f4,#e6e6e6);border:1px solid #ddd;display:flex;align-items:center;justify-content:space-between;padding:0 6px 0 8px;color:#b5b5b5;font-size:9px}

.main-nav{left:46px;top:110px;width:735px;height:25px;border-bottom:1px solid var(--rule)}
.main-nav a{position:absolute;top:0;font-size:12.5px;color:var(--brand);white-space:nowrap}
.main-nav .current::after{content:"";position:absolute;left:50%;bottom:-13px;margin-left:-5px;border:5px solid transparent;border-bottom-color:#b9cfdb}

.slider{left:44px;top:154px;width:737px;height:219px;background:var(--frame);border-radius:5px;box-shadow:0 2px 3px rgba(0,0,0,.3)}
.slide-tab{position:absolute;top:7px;width:36px;height:206px;background:var(--tab);border:1px solid #222;color:var(--white);font-size:13px;font-weight:700}
.slide-tab span{position:absolute;bottom:6px;left:0;width:100%;text-align:center}
.slide-tab.active{background:var(--tab-active)}
.tab-dots{position:absolute;left:13px;bottom:24px;display:flex;flex-direction:column;gap:2px}
.tab-dots i{display:block;width:7px;height:7px;border-radius:50%;background:#111}
.tab-dots i.on{background:#2b6f95}
.slide-photo{left:117px;top:6px;width:412px;height:211px;background:linear-gradient(100deg,#0b1b3a 0%,#1b4f8a 40%,#6d9cc9 70%,#c4d8ea 100%)}
.slide-head{left:128px;top:88px;font-family:"Roboto Condensed",Arial,sans-serif;font-weight:700;color:var(--white);line-height:1;white-space:nowrap}
.slide-head .l1{font-size:38px;text-shadow:0 2px 3px rgba(0,0,0,.6)}
.slide-head .l2{font-size:27px;margin-left:40px;margin-top:2px;color:#e8eef4;text-shadow:0 2px 3px rgba(0,0,0,.5)}
.slide-head .l3{font-size:27px;margin-left:128px;margin-top:3px;color:#e8eef4;text-shadow:0 2px 3px rgba(0,0,0,.5)}
.slide-panel{left:529px;top:6px;width:162px;height:211px;background:var(--panel);color:var(--white);padding:42px 8px 0 8px;font-size:9.6px;line-height:12px;text-align:justify;text-shadow:0 1px 1px rgba(0,0,0,.4)}
.slide-more{position:absolute;left:8px;bottom:14px;display:flex;align-items:center;gap:5px;color:#2a78b0;font-size:9px}

.feature{width:222px;height:115px}
.feature-icon{position:absolute;left:0;top:0;width:66px;height:66px;background:var(--white);border:1px solid #ddd;border-radius:3px;box-shadow:1px 2px 3px rgba(0,0,0,.15);padding:6px}
.feature-icon div{width:100%;height:100%;border-radius:3px}
.feature-title{position:absolute;left:66px;top:46px;width:160px;height:23px;border-top:1px solid #e6e6e6;border-bottom:1px solid #e6e6e6;background:linear-gradient(#fff,#f7f7f7);padding:5px 0 0 11px;font-size:11.5px;color:var(--brand);white-space:nowrap}
.feature-text{position:absolute;left:4px;top:88px;width:218px;font-size:8.6px;line-height:12.5px;color:var(--muted);text-align:justify}
.feature-text .more{float:right;color:var(--brand)}

.section-rule{height:2px;background:linear-gradient(90deg,transparent,#e2e2e2 10%,#e2e2e2 90%,transparent)}

.about-title,.news-title{font-size:11.5px;color:var(--brand)}
.about-text{left:50px;top:771px;width:398px;font-size:8.6px;line-height:12.6px;color:var(--text);text-align:justify}
.about-text p+p{margin-top:12px}
.about-text .more{display:block;text-align:right;color:var(--brand);margin-top:-12px}
.news-title{left:518px;top:743px;width:255px;padding-bottom:8px;border-bottom:1px solid #e2e2e2}
.news-item{left:518px;width:260px;padding-left:40px}
.news-item h4{font-size:9px;font-style:italic;font-weight:700;color:#333;margin-bottom:5px}
.news-item p{font-size:8.6px;line-height:12.5px;color:#444}
.news-item .more{float:right;color:var(--brand)}
.news-item svg{position:absolute;left:0;top:0}
.news-split{left:518px;top:833px;width:255px;border-top:1px dashed #d4d4d4}

.foot-col{font-size:8.6px;line-height:15px;color:#7a7a7a}
.foot-col h5{color:#8e8e8e;font-size:8.6px}
.video{left:593px;top:957px;width:164px;height:110px;background:#1c1c1c}
.video-still{position:absolute;left:0;top:12px;width:164px;height:84px;background:linear-gradient(120deg,#6b6b5c,#b8b6a5 60%,#e6e4da)}
.video-title{position:absolute;left:6px;top:2px;color:var(--white);font-size:7px}
.video-caption{position:absolute;left:22px;top:56px;color:var(--white);font-weight:700;font-size:11.5px;line-height:12px;text-shadow:0 1px 2px #000}
.video-bar{position:absolute;left:0;bottom:0;width:100%;height:14px;background:#111;display:flex;align-items:center;gap:8px;padding:0 6px;color:#ccc;font-size:7px}

.bottom-bar{left:45px;top:1081px;width:735px;height:87px;background:var(--footer-bg);border-radius:4px}
.legal{left:15px;top:20px;font-size:8.6px;color:#666;line-height:25px}
.contact{left:358px;top:20px;font-size:8.6px;color:#666;line-height:15px}
.promo-art{left:521px;top:13px;width:200px;height:61px;background:linear-gradient(90deg,#fff,#eadfe1 35%,#dbe7ed 65%,#f4f4f4)}
</style>
</head>
<body>

<div class="abs top-strip"></div>

<a class="abs brand" href="http://vantrelux-newsite.pagemorrowhost.com/index">
  <span class="brand-dot"></span><span class="brand-name">vantrelux</span>
</a>

<div class="abs search">
  <span>Search</span>
  <svg width="22" height="22" viewBox="0 0 22 22"><circle cx="9" cy="9" r="6.5" fill="#eef4f8" stroke="#8a9aa6" stroke-width="2"/><line x1="14" y1="14" x2="20" y2="20" stroke="#444" stroke-width="3" stroke-linecap="round"/></svg>
</div>

<nav class="abs main-nav">
  <a class="current" style="left:10px" href="#">HOME</a>
  <a style="left:71px" href="#">PRODUCTS</a>
  <a style="left:158px" href="#">SERVICES</a>
  <a style="left:243px" href="#">SOLUTIONS</a>
  <a style="left:338px" href="#">RESOURCES</a>
  <a style="left:436px" href="#">CUSTOMER STORIES</a>
  <a style="left:583px" href="#">ABOUT US</a>
  <a style="left:669px" href="#">CONTACT</a>
</nav>

<section class="abs slider">
  <div class="slide-tab" style="left:8px"><div class="tab-dots"><i></i><i></i><i></i></div><span>1</span></div>
  <div class="slide-tab" style="left:46px"><span>2</span></div>
  <div class="slide-tab active" style="left:84px;width:34px"><div class="tab-dots"><i></i><i class="on"></i></div><span>3</span></div>
  <div class="abs slide-photo" role="img" aria-label="Blue data-stream photograph behind the slide headline"></div>
  <div class="abs slide-head">
    <div class="l1">System Requirements</div>
    <div class="l2">Relate business processes</div>
    <div class="l3">to IT systems capability</div>
  </div>
  <div class="abs slide-panel">
    Traditional methods of of developing system requirem­ents often result in projects running over time, over budget and require ongoing change to deliver expected benefits. According to Marlowe Research the project failure rate is in the order of 15:1.
    <a class="slide-more" href="#"><svg width="11" height="11" viewBox="0 0 11 11"><circle cx="5.5" cy="5.5" r="5" fill="#eee"/><path d="M5.5 2.5v6M2.5 5.5h6" stroke="#555" stroke-width="1.4"/></svg>Read more...</a>
  </div>
  <div class="slide-tab" style="left:692px;width:37px"><span>4</span></div>
</section>

<article class="abs feature" style="left:46px;top:400px">
  <div class="feature-icon"><div role="img" aria-label="Icon of three linked figures" style="background:#e9d3cf"></div></div>
  <h3 class="feature-title">Knowledge Management</h3>
  <p class="feature-text">The challenge for a traditional knowledge management system is that it simply stores, indexes and tags documents. <a class="more" href="#">more</a></p>
</article>
<article class="abs feature" style="left:303px;top:400px">
  <div class="feature-icon"><div role="img" aria-label="Icon of a checklist with an award ribbon" style="background:#f4e3b5"></div></div>
  <h3 class="feature-title">Continuous Improvement</h3>
  <p class="feature-text">The implementation of a continuous improvement model is very different to traditional project based approaches. <a class="more" href="#">more</a></p>
</article>
<article class="abs feature" style="left:561px;top:400px">
  <div class="feature-icon"><div role="img" aria-label="Icon of a document turning into binary data" style="background:#d5e6e8"></div></div>
  <h3 class="feature-title">Business Transformation</h3>
  <p class="feature-text">Transformation initiatives involving large systems implementations require management of many moving parts. <a class="more" href="#">more</a></p>
</article>

<article class="abs feature" style="left:46px;top:555px">
  <div class="feature-icon"><div role="img" aria-label="Icon of two gears" style="background:#e6d4ee"></div></div>
  <h3 class="feature-title">System Requirements</h3>
  <p class="feature-text">Traditional methods of of developing system requirements often result in projects running over time,over budget &amp; ongoing change. <a class="more" href="#">more</a></p>
</article>
<article class="abs feature" style="left:303px;top:555px">
  <div class="feature-icon"><div role="img" aria-label="Icon of a process flow diagram" style="background:#d6e5f4"></div></div>
  <h3 class="feature-title">Business Process Modeling</h3>
  <p class="feature-text">Typically traditional business process mapping is very effective at visualizing and creating a better understanding of business processes. <a class="more" href="#">more</a></p>
</article>
<article class="abs feature" style="left:561px;top:555px">
  <div class="feature-icon"><div role="img" aria-label="Icon of a courthouse and gavel" style="background:#d3ead3"></div></div>
  <h3 class="feature-title">Governance &amp; Compliance</h3>
  <p class="feature-text">Corporate governance ensures compliance and accountability in the operations of your business. Governance provides the framework. <a class="more" href="#">more</a></p>
</article>

<div class="abs section-rule" style="left:38px;top:711px;width:752px"></div>

<h2 class="abs about-title" style="left:48px;top:743px">We power and de-risk business transformations</h2>
<div class="abs about-text">
  <p>Operational excellence and business transformation is achieved by understanding and capturing every detail of your business. High performing companies have a single view of the complex relationships between systems, processes and people supported by in depth organizational knowledge. Vantrelux's Operational Business Management System (OBMS) empowers and de-risks large transformation initiatives enabling continuous improvement for high performing organizations.</p>
  <p>An OBMS captures the DNA of your business. It links people, processes and systems in a way that visualizes how your organization works today, and how it may change in the future. This information is managed in a re-usable and extendable framework and is distributed to the many stakeholders in a form that meets their individual needs.</p>
  <a class="more" href="#">Read more+</a>
</div>

<h2 class="abs news-title">NEWS &amp; EVENTS</h2>
<div class="abs news-item" style="top:771px">
  <svg width="32" height="32" viewBox="0 0 32 32"><rect x="1" y="3" width="30" height="28" rx="2" fill="#fff" stroke="#777"/><rect x="1" y="3" width="30" height="8" fill="#2f86c8"/><text x="5" y="9.5" font-size="5" fill="#fff" font-family="Arial">SEP</text><text x="16" y="28" font-size="17" font-weight="700" text-anchor="middle" fill="#222" font-family="Arial">12</text></svg>
  <h4>SYDNEY: Elements of Improvement</h4>
  <p>Lorem ipsum dolor sit amet, consectetur adipisicing elit, sed do eiusmod tempor incididunt ut labore et dolore magna aliqua. <a class="more" href="#">More....</a></p>
</div>
<div class="abs news-split"></div>
<div class="abs news-item" style="top:844px">
  <svg width="32" height="32" viewBox="0 0 32 32"><rect x="1" y="3" width="30" height="28" rx="2" fill="#fff" stroke="#777"/><rect x="1" y="3" width="30" height="8" fill="#2f86c8"/><text x="5" y="9.5" font-size="5" fill="#fff" font-family="Arial">SEP</text><text x="16" y="28" font-size="17" font-weight="700" text-anchor="middle" fill="#222" font-family="Arial">12</text></svg>
  <h4>MELBOURNE: BPI &amp; Business Process</h4>
  <p>Lorem ipsum dolor sit amet, consectetur adipisicing elit, sed do eiusmod tempor incididunt ut labore et dolore magna aliqua. <a class="more" href="#">More....</a></p>
</div>

<div class="abs section-rule" style="left:42px;top:935px;width:736px"></div>

<div class="abs foot-col" style="left:47px;top:957px">
  <h5>PRODUCTS</h5>
  <div>Modelwiki</div><div>Vantrelux Modeler</div><div>- System Requirements Modeler</div><div>- Performance Improvement Modeler</div><div>- Enterprise Architect Modeler</div><div>- Corporate Governance Modeler</div>
</div>
<div class="abs foot-col" style="left:263px;top:957px">
  <h5>SERVICES</h5>
  <div>Coaching &amp; Mentoring</div><div>Technical Services</div><div>&nbsp;</div>
  <h5>NEWS &amp; EVENTS</h5>
  <div>Announcements</div><div>Technical Notes</div>
</div>
<div class="abs foot-col" style="left:419px;top:957px">
  <h5>TRAINING &amp; SUPPORT</h5>
  <div>Text-Based Tutorials</div><div>Tutorial Movies</div><div>Knowledge Base</div><div>Forums</div><div>Training Courses</div>
</div>

<div class="abs video">
  <div class="video-still" role="img" aria-label="Video still of a presenter at a whiteboard"></div>
  <div class="video-title">Vantrelux Systems Lifec</div>
  <svg class="abs" style="left:67px;top:31px" width="30" height="20" viewBox="0 0 30 20"><rect width="30" height="20" rx="4" fill="rgba(0,0,0,.7)"/><path d="M12 5l8 5-8 5z" fill="#fff"/></svg>
  <div class="video-caption">VIDEO TO COME<br>FOR THIS PAGE</div>
  <div class="video-bar">
    <svg width="8" height="8" viewBox="0 0 8 8"><path d="M1 0l7 4-7 4z" fill="#ccc"/></svg>
    <svg width="9" height="8" viewBox="0 0 9 8"><path d="M0 2.5h2l3-2.5v8l-3-2.5H0z" fill="#ccc"/></svg>
    <span style="margin-left:8px">00:00 / 12:10</span>
  </div>
</div>

<footer class="abs bottom-bar">
  <div class="abs legal">
    <div>TERMS &amp; CONDITIONS | PRIVACY POLICY | MAINTENANCE POLICY</div>
    <div>© Copyright VANTRELUX 2012 - All Rights Reserved</div>
  </div>
  <div class="abs contact">
    <div>CONTACT INFORMATION</div><div>Address :</div><div>Phone No. :</div><div>Email Id :</div>
  </div>
  <div class="abs promo-art" role="img" aria-label="Promotional banner with a double helix illustration"></div>
</footer>

</body>
</html>
```